Podiatry clinic requires a modern revamp and editing of existing website.

I would like a fresh new look and updated information for my current business website. An easy to navigate site with prominent address and phone number for call to action. We are a podiatry clinic that focuses on general and sports podiatry.
I would like 4 pages; including Home page, About Us, Services & Contact.
www.brambleridgepodiatry.net

Target Market(s)

Active working professionals.

Industry/Entity Type

Medical

Coding

Coded - Design and coding required

Number of Pages Required

4 page

Font styles to use
Sans Serif

Colors
6b449b

Requirements
Must have
• A modern look with logo and active images; clean and uncluttered. Visible phone number and address for call to action.
• 4 pages - Home, About Us, Services, Contact.
• Home page - update address & service logos.
• About Us - update of personal information.
• Services - Revamp of existing page.
• Contact page to include Google map, email & phone number.
Nice to have
• Ability to add content easily; eg. a blog or adding video onto Home page.
• Link to Facebook page.

```html
<!DOCTYPE html>
<html lang="en">
<head>
<meta charset="utf-8">
<title>Bramble Ridge Podiatry</title>
<link href="https://fonts.googleapis.com/css2?family=Arimo:wght@400;700&family=Raleway:wght@400;500&family=Roboto+Condensed:wght@700&display=swap" rel="stylesheet">
<style>
:root{
  --purple:#6b449b;
  --purple-dark:#3b2c6e;
  --lilac:#9d86c4;
  --orange:#ff8a3d;
  --grey-head:#5a5a5a;
  --grey-bar:#5b5b5b;
  --ink:#2b2b3a;
  --white:#fff;
}
*{margin:0;padding:0;box-sizing:border-box}
html,body{width:807px;height:1200px;overflow:hidden;background:var(--white)}
body{position:relative;font-family:"Arimo",Arial,sans-serif;color:var(--ink)}
.abs{position:absolute}
.hero{left:0;top:0;width:807px;height:345px;background:linear-gradient(180deg,#8a8fa0 0%,#6f7560 38%,#5e6a45 55%,#55565a 75%,#47484c 100%);border-bottom:2px solid var(--purple-dark)}
.social-top{top:6px;left:604px;display:flex;gap:19px}
.social-top span{width:10px;height:10px;border-radius:50%;background:var(--white);opacity:.9}
.header{left:84px;top:22px;width:635px;height:56px;background:rgba(255,255,255,.95)}
.logo-box{left:0;top:0;width:96px;height:56px;background:var(--lilac);display:flex;align-items:center;justify-content:center;text-align:center;padding:4px}
.logo-name{font-family:"Raleway",sans-serif;font-weight:500;font-size:11px;line-height:13px;color:var(--white)}
.nav{left:284px;top:0;height:56px;display:flex;font-size:10px;color:#444}
.nav a{display:flex;align-items:center;padding:0 8px;height:56px;color:#444;text-decoration:none}
.nav a.active{background:var(--orange);color:var(--white)}
.divider{left:499px;top:11px;width:1px;height:34px;background:#333}
.phone-ico{left:520px;top:17px}
.call-label{left:548px;top:17px;font-size:10px;color:var(--orange)}
.call-num{left:546px;top:29px;font-size:13.5px;color:#222}
.cap1{left:179px;top:164px;height:29px;width:339px;background:var(--orange);color:var(--white);font-family:"Roboto Condensed",sans-serif;font-weight:700;font-size:15px;line-height:29px;padding-left:3px;white-space:nowrap}
.cap1 b{font-size:18px}
.cap2{left:179px;top:196px;height:29px;width:184px;background:var(--purple-dark);color:var(--white);font-family:"Roboto Condensed",sans-serif;font-weight:700;font-size:16px;line-height:29px;padding-left:7px}
.arrow{top:165px;width:35px;height:35px;background:rgba(255,255,255,.35);display:flex;align-items:center;justify-content:center}
.dots{top:335px;left:356px;display:flex;gap:4px}
.dots span{width:24px;height:3px;background:rgba(255,255,255,.55)}
.dots span:first-child{background:var(--white)}
h2{font-family:"Raleway",sans-serif;font-weight:400;text-align:center;position:absolute}
.welcome-title{left:0;width:807px;top:370px;font-size:21px;color:var(--purple-dark)}
.rule{height:0;border-top:1px dotted #b0b0b0}
.welcome-body{left:78px;top:405px;width:651px}
.intro{text-align:center;font-size:10.2px;line-height:18.5px;color:#333}
.enquiry{margin-top:7px;text-align:center;font-size:10px;font-weight:700;line-height:16.5px;color:#222}
.shadow-line{left:5px;top:543px;width:797px;height:8px;background:radial-gradient(ellipse at top,rgba(0,0,0,.28),rgba(0,0,0,0) 70%)}
.services-title{left:0;width:807px;top:573px;font-size:20px;color:var(--purple-dark)}
.card{top:619px;width:201px}
.card-head{height:33px;background:var(--grey-head);color:var(--white);font-family:"Raleway",sans-serif;font-size:14px;line-height:33px;text-align:center}
.card-img{height:101px;border:2px solid #cde3ea;border-top:0;box-shadow:0 2px 3px rgba(0,0,0,.25)}
.card-text{margin-top:14px;text-align:center;font-size:9px;line-height:16.5px;color:#222;padding:0 8px}
.affil{left:0;top:846px;width:807px;height:154px;background:var(--orange)}
.affil-title{left:0;width:807px;top:22px;font-size:21px;color:var(--purple-dark)}
.badge{top:74px;width:139px;height:53px;background:var(--white);border:1px solid #999;display:flex;align-items:center;justify-content:center}
.badge i{display:block;width:100px;height:24px;border-radius:4px}
.footer{left:0;top:1000px;width:807px;height:170px;background:var(--lilac);font-family:"Raleway",sans-serif;color:var(--white)}
.f-head{font-size:12.5px;color:#3c3c50;padding-bottom:7px;border-bottom:1px solid rgba(255,255,255,.35)}
.f-col{top:18px}
.links{list-style:none;margin-top:8px;font-size:9px;line-height:17px;color:#1e1e30;white-space:nowrap}
.links li::before{content:"›";margin-right:8px;color:#eee}
.contact-row{display:flex;align-items:flex-start;gap:8px;font-size:9px;line-height:11px;color:#1e1e30;padding:10px 0;border-bottom:1px solid rgba(255,255,255,.3);width:166px}
.hours p{font-size:9px;line-height:12.5px;color:#1e1e30;padding:6px 0;border-bottom:1px solid rgba(255,255,255,.3);width:110px}
.vsep{top:40px;width:1px;height:80px;background:rgba(255,255,255,.35)}
.f-logo{left:612px;top:50px;width:110px;font-size:15px;font-weight:500;line-height:19px;color:var(--white)}
.bottom{left:0;top:1170px;width:807px;height:30px;background:var(--grey-bar);color:#eee;font-family:"Raleway",sans-serif;font-size:9.5px;line-height:30px;padding-left:88px}
.bottom-social{left:654px;top:1174px;display:flex;gap:7px}
.bottom-social span{width:22px;height:22px;border-radius:50%;background:#dedede}
</style>
</head>
<body>

<section class="hero abs" role="img" aria-label="Close-up of a runner's shoes striding along a sunlit park path"></section>
<div class="social-top abs" aria-label="Social links"><span></span><span></span><span></span><span></span></div>

<header class="header abs">
  <div class="logo-box abs"><span class="logo-name">Bramble Ridge Podiatry</span></div>
  <nav class="nav abs">
    <a class="active" href="#">Home</a><a href="#">About Us</a><a href="#">Services</a><a href="#">Contact</a>
  </nav>
  <div class="divider abs"></div>
  <svg class="phone-ico abs" width="22" height="22" viewBox="0 0 22 22"><circle cx="11" cy="11" r="9.5" fill="none" stroke="#333" stroke-width="1.3"/><path d="M8 6c-1 1-1.5 3 0 6s4 4.5 5 4l1.2-1.2-2-1.8-1 .8c-1-.5-2-2-2.4-3l1-1-1.2-2.4z" fill="#333"/></svg>
  <div class="call-label abs">Call Us Today</div>
  <div class="call-num abs">1300 555 018</div>
</header>

<div class="cap1 abs"><b>Bramble Ridge Podiatry</b> is a Podiatry clinic in the</div>
<div class="cap2 abs">Heart of Melbourne CBD</div>
<div class="arrow abs" style="left:0"><svg width="14" height="12" viewBox="0 0 14 12"><path d="M7 1 2 6l5 5M12 1 7 6l5 5" fill="none" stroke="#fff" stroke-width="1.5"/></svg></div>
<div class="arrow abs" style="left:772px"><svg width="14" height="12" viewBox="0 0 14 12"><path d="M2 1l5 5-5 5M7 1l5 5-5 5" fill="none" stroke="#fff" stroke-width="1.5"/></svg></div>
<div class="dots abs"><span></span><span></span><span></span></div>

<h2 class="welcome-title">Welcome to Bramble Ridge Podiatry</h2>
<div class="rule abs" style="left:244px;top:398px;width:310px"></div>
<div class="welcome-body abs">
  <p class="intro">Bramble Ridge Podiatry is a Podiatry clinic in the heart of Melbourne CBD. We are located between Fern &amp; Ash Streets in the Harbour Lane Centre / Linden Court Complex. Our podiatrists are fully qualified health professionals who are able to diagnose, treat, manage or help to prevent all medical conditions that affect the feet and lower limb. We provide General Podiatry Treatment and some Specialised Services in relation to various foot conditions, including Sports Injuries, Orthotic Therapy and Nail Surgery.</p>
  <p class="enquiry">For Appointments or Enquiries please<br>call us on 1300 555 018 &nbsp;or email: &nbsp;&nbsp;info@brambleridgepodiatry.net</p>
</div>
<div class="shadow-line abs"></div>

<h2 class="services-title">Our Services</h2>
<div class="rule abs" style="left:334px;top:600px;width:133px"></div>

<article class="card abs" style="left:90px">
  <div class="card-head">Sports Injuries</div>
  <div class="card-img" role="img" aria-label="Basketball player seated on a court holding an injured ankle" style="background:linear-gradient(135deg,#c9b79a,#a8876a 55%,#7a5a45)"></div>
  <p class="card-text">Lorem ipsum dolor sit amet, consectetuer adipiscing elit, sed diam nonummy nibh euismod tincidunt ut laoreet.</p>
</article>
<article class="card abs" style="left:304px">
  <div class="card-head">Orthotic Therapy</div>
  <div class="card-img" role="img" aria-label="Podiatrist fitting an orthotic insole to a patient's foot" style="background:linear-gradient(135deg,#e6e4df,#c8c0b4 55%,#9a948c)"></div>
  <p class="card-text">Lorem ipsum dolor sit amet, consectetuer adipiscing elit, sed diam nonummy nibh euismod tincidunt ut laoreet.</p>
</article>
<article class="card abs" style="left:517px">
  <div class="card-head">Nail Surgery</div>
  <div class="card-img" role="img" aria-label="Gloved hands giving an injection to a toe before nail surgery" style="background:linear-gradient(135deg,#7e8a94,#d9c8bb 55%,#b49585)"></div>
  <p class="card-text">Lorem ipsum dolor sit amet, consectetuer adipiscing elit, sed diam nonummy nibh euismod tincidunt ut laoreet.</p>
</article>

<section class="affil abs">
  <h2 class="affil-title">Our Affiliations</h2>
  <div class="rule abs" style="left:334px;top:50px;width:140px;border-color:#c9601f"></div>
  <div class="badge abs" style="left:103px"><i style="background:#dbe4f2"></i></div>
  <div class="badge abs" style="left:254px"><i style="background:#d6e0ee"></i></div>
  <div class="badge abs" style="left:406px"><i style="background:#e8e8e8"></i></div>
  <div class="badge abs" style="left:557px"><i style="background:#cfe9d8"></i></div>
</section>

<footer class="footer abs">
  <div class="f-col abs" style="left:89px;width:110px">
    <div class="f-head" style="width:90px">Quick Links</div>
    <ul class="links">
      <li>Consulting</li><li>Inspections</li><li>Training</li><li>General Contracing</li><li>Clients</li><li>Contact Us</li>
    </ul>
  </div>
  <div class="vsep abs" style="left:211px"></div>
  <div class="f-col abs" style="left:239px;width:166px">
    <div class="f-head">Contact Details</div>
    <div class="contact-row"><svg width="8" height="11" viewBox="0 0 8 11"><path d="M4 0a4 4 0 0 0-4 4c0 3 4 7 4 7s4-4 4-7a4 4 0 0 0-4-4zm0 5.5A1.5 1.5 0 1 1 4 2.5a1.5 1.5 0 0 1 0 3z" fill="#222"/></svg><span>Suite 214 / 62 Harbour<br>Lane &nbsp;Melbourne &nbsp;3000</span></div>
    <div class="contact-row" style="padding:14px 0"><svg width="10" height="10" viewBox="0 0 10 10"><path d="M2 0c-1 1-2 2 0 5s4 5 5 5l2-2-2-2-1 1C5 6.5 3.5 5 3 4l1-1-2-3z" fill="#222"/></svg><span>1300 555 018</span></div>
    <div class="contact-row" style="border:0;padding:14px 0 0 2px"><svg width="10" height="8" viewBox="0 0 10 8"><rect width="10" height="8" fill="#222"/><path d="M0 0l5 4 5-4" fill="none" stroke="#9d86c4"/></svg><span>info@brambleridgepodiatry.net</span></div>
  </div>
  <div class="vsep abs" style="left:437px"></div>
  <div class="f-col abs hours" style="left:466px;width:120px">
    <div class="f-head">Hours of Operation</div>
    <p>Monday to Friday<br>10:00am to 07:00pm</p>
    <p style="padding-top:10px">Saturday<br>10:00am to 05:00pm</p>
    <p style="border:0;padding-top:10px">Sunday<br>By Appointment Only</p>
  </div>
  <div class="f-logo abs">Bramble Ridge Podiatry</div>
</footer>

<div class="bottom abs">Copyright © 2016 Northwind Web Studio. &nbsp;All Right Reserved.</div>
<div class="bottom-social abs"><span></span><span></span><span></span></div>

</body>
</html>
```